July 2022 Industrial Manufacturer Product Expo Mexico City

We manufacture large screws and fastners for large Mining equipment, Trains, large ships, airplanes, wind turbines, and so on. We also do custom work base on the customer needs. No matter the size we can make it.
We have a Expo coming up with companies all over the world. We have to stand out we are a family own business so our customer service will be above and beyond anyone can provide. We do not have a sales force to push our products and services we provide one on one service.
Plus@!! I'm looking for anything that you designers can come up with if it was your company to put on a business card, plus i want to do a 1 or 2 sided pamphlet, and then a website. We make Speciality Bolts for large mining equipment these bolts can be 3 to 4 foot long!!! Plus fasteners, Nuts, washers, any, size, strengths, special materials, we offer more of a ono on one customer service, We are a small company, family own, but can fulfill any type of orders. We can also provide special time lines for emergency orders. "We keep the machines running we here at KRV don't believe in down time" We want to hear any slogan based on our company to stand out.
Thanks i really appreciate all your work and options that we have to pick on. Plus just a thought we could possibly want to entertain a experience Marketing internet help maybe a employment possibility. Thanks

I need 2 cards one in Spanish and English Like the steel back ground maybe send me in some bright red and blue writing Same with the Black cards Please remove the word Military The logo KRV maybe integrate a picture of a Bolt 🔩 Thank you

Still looking for I need 2 cards one in Spanish and English Like the steel back ground maybe send me in some bright red and blue writing Same with the Black cards try bright writing Please remove the word Military The logo KRV maybe integrate a picture of a Bolt 🔩 Plus will need the company to make a brochure and website next Thank you

Target Market(s)

Large Mining, Ship, Train, Green Energy, VELM, and Government equipment. Throughout the World

Industry/Entity Type

We can Custom Manufacture any type of Fastners for Mining equipment, Trains, Ships, Green energy, Governments, or military projects. wind turbines,

Contact Information for Business Card

I attached the name and contact info that's on a card, plus the Company Logo. Would like industrial looking background with Bright Colors that will stand out!! If we can insert somewhere maybe on back that we "Custom Manufacture Any Size or Quantity Fastners for Large Mining Equipment, Trains, Ships, Green Energy Equipment or Government Projects

Font styles to use
Other font styles liked:
• You Pick, has to be bold, colorful standout, Professional looking Beable to read it.

Colors

Designer to choose colors to be used in the design.

Requirements
Must have
• Need in Spanish and English TO STANDOUT FROM THE REST OF THE EXPO!! See Business card details, Rounded corners
Nice to have
• Can i see some of the darker cards with Bright Red and Blue letters I like to see the different type of card material, heavy thickness, plastic, transparent, Metal types, Bright Colors, I saw like Raised letters like on the logo.

```html
<!DOCTYPE html>
<html lang="es">
<head>
<meta charset="utf-8">
<title>KRV – Tarjetas de presentación</title>
<link href="https://fonts.googleapis.com/css2?family=Roboto:wght@400;700;900&family=Roboto+Condensed:wght@400;700&display=swap" rel="stylesheet">
<style>
  :root {
    --backdrop: #d6d7d9;
    --paper: #ffffff;
    --navy: #0d1a78;
    --navy-deep: #0a0f5e;
    --blue-bright: #0a86d2;
    --blue-mid: #0a55b8;
    --graphite: #2b2b31;
    --edge: #1e8fd6;
  }
  * { box-sizing: border-box; margin: 0; padding: 0; }
  html, body { width: 1200px; height: 800px; overflow: hidden; }
  body {
    background: var(--backdrop);
    font-family: "Roboto", Arial, sans-serif;
    display: flex;
    align-items: center;
    justify-content: center;
    gap: 50px;
  }
  .card {
    width: 540px;
    height: 310px;
    border-radius: 24px;
    position: relative;
    overflow: hidden;
    box-shadow: 0 0 0 2px var(--edge), 0 14px 30px rgba(0,0,0,.18);
  }

  /* Front */
  .card--front { background: var(--paper); }
  .front__brand {
    position: absolute;
    top: 34px; left: 0; right: 0;
    text-align: center;
  }
  .brand-name {
    font-family: "Roboto", Arial, sans-serif;
    font-weight: 900;
    font-size: 78px;
    line-height: 1;
    letter-spacing: 6px;
    color: var(--graphite);
  }
  .brand-tagline {
    font-family: "Roboto Condensed", Arial, sans-serif;
    font-size: 17px;
    letter-spacing: .5px;
    color: var(--navy);
    margin-top: 8px;
  }
  .front__band {
    position: absolute;
    left: 0; right: 0;
    top: 168px;
    height: 58px;
    background: linear-gradient(90deg, var(--navy-deep) 0%, var(--blue-mid) 45%, var(--blue-bright) 70%, var(--navy) 100%);
    text-align: center;
    color: #fff;
    padding-top: 8px;
  }
  .holder-name {
    font-weight: 900;
    font-size: 22px;
    letter-spacing: .5px;
  }
  .holder-role {
    font-family: "Roboto Condensed", Arial, sans-serif;
    font-size: 13px;
    margin-top: 2px;
  }
  .front__contact {
    position: absolute;
    left: 0; right: 0;
    top: 252px;
    display: flex;
    justify-content: center;
    align-items: center;
    gap: 6px;
    font-family: "Roboto Condensed", Arial, sans-serif;
    font-size: 14px;
    color: var(--graphite);
  }
  .contact-item { display: inline-flex; align-items: center; gap: 4px; }
  .contact-item + .contact-item { margin-left: 6px; }
  .contact-icon { width: 12px; height: 12px; fill: var(--navy); }

  /* Back */
  .card--back {
    background: linear-gradient(150deg, var(--blue-bright) 0%, var(--blue-mid) 45%, var(--navy-deep) 100%);
  }
  .back__brand {
    position: absolute;
    top: 92px; left: 0; right: 0;
    text-align: center;
  }
  .back__brand .brand-name {
    color: #15161c;
    font-size: 96px;
    letter-spacing: 8px;
  }
  .back__brand .brand-tagline {
    color: #ffffff;
    font-size: 19px;
    margin-top: 10px;
  }
</style>
</head>
<body>

  <section class="card card--front" aria-label="Frente de la tarjeta">
    <div class="front__brand">
      <div class="brand-name">KRV</div>
      <div class="brand-tagline">FABRICACION Y DISTRIBUCION DE TORNILLOS</div>
    </div>

    <div class="front__band">
      <div class="holder-name">LIC. MARISOL ANDRADE RUIZ</div>
      <div class="holder-role">Cotizaciones en</div>
    </div>

    <div class="front__contact">
      <span class="contact-item">
        <svg class="contact-icon" viewBox="0 0 24 24" aria-hidden="true"><path d="M6.6 10.8a15.1 15.1 0 0 0 6.6 6.6l2.2-2.2a1 1 0 0 1 1-.25 11.4 11.4 0 0 0 3.6.57 1 1 0 0 1 1 1V20a1 1 0 0 1-1 1A17 17 0 0 1 3 4a1 1 0 0 1 1-1h3.5a1 1 0 0 1 1 1c0 1.25.2 2.45.57 3.57a1 1 0 0 1-.25 1z"/></svg>
        5550142876
      </span>
      <span class="contact-item">
        <svg class="contact-icon" viewBox="0 0 24 24" aria-hidden="true"><path d="M7 1h10a2 2 0 0 1 2 2v18a2 2 0 0 1-2 2H7a2 2 0 0 1-2-2V3a2 2 0 0 1 2-2zm0 3v14h10V4z"/></svg>
        5550193354
      </span>
      <span class="contact-item">
        <svg class="contact-icon" viewBox="0 0 24 24" aria-hidden="true"><path d="M2 5h20v14H2zm2 2v.5l8 5 8-5V7z"/></svg>
        krvtornillos.ventas@correo.mx
      </span>
    </div>
  </section>

  <section class="card card--back" aria-label="Reverso de la tarjeta">
    <div class="back__brand">
      <div class="brand-name">KRV</div>
      <div class="brand-tagline">FABRICACION Y DISTRIBUCION DE TORNILLOS</div>
    </div>
  </section>

</body>
</html>
```